uk based ecommerce website requires fresh look ,high quality look and feel

we are a web based company selling eco friendly ground reinforcement grids to diy and construction sectors
our existing website is www.pondermeshpaths.co.uk ,

we have already updated the logo so that is the branding sorted .so we need a ecommerce website that is very much up-to date in design and layout and which has content management system for ease of use so that we can add products and information as required.

Use current logo as reference for colour scheme.
www.pondermeshpaths.co.uk

The current website has 6 pages accessible through the navigation bar, I would now like 5 pages, removing the need for the Trade Enquiries page possibly have it with along with contact us.

Target Market(s)

construction industry , diy end users,
retail market, landscapers, gardeners

Industry/Entity Type

Construction

Font styles to use
Other font styles liked:
• logo font prometo

Colors
f78f20
9bcb3c

Requirements
Must have
• logo colours and logo design in website with cms responsive design for tablet and mobile devices
• expect content to work flawlessly and look great across all devices
• HTML 5 custom design with coding as required
• must have good experiance in ecommerce website design
• eye catching, high quality look and feel and very user friedly ,very up-to date.
Nice to have
• picture slider show
• explain in writing what exactly i am getting in my ecommerce website
Should not have
• plain , basic design , old fashion looking ,cheap look

```html
<!DOCTYPE html>
<html lang="en">
<head>
<meta charset="utf-8">
<title>Pondermesh Ground Solutions</title>
<link rel="stylesheet" href="https://fonts.googleapis.com/css2?family=Open+Sans:wght@400;600;700;800&family=Roboto+Condensed:wght@400;700&display=swap">
<style>
:root{
  --orange:#f78f20;
  --green:#9bcb3c;
  --ink:#333;
  --footer:#3b3b3b;
  --panel:#f1f1f1;
}
*{box-sizing:border-box;margin:0;padding:0}
html,body{width:1200px;height:2826px;overflow:hidden}
body{font-family:"Open Sans",Arial,sans-serif;color:var(--ink);background:#fff;position:relative}
a{color:inherit;text-decoration:none}
.block{position:absolute;left:0;width:1200px}

/* header */
.site-header{top:0;height:143px;background:#fff}
.topbar{position:absolute;right:0;top:0;height:30px;width:640px;background:var(--orange);display:flex;align-items:center;justify-content:flex-end;padding-right:145px;color:#fff;font-size:10px;font-weight:600;gap:6px}
.topbar strong{font-size:13px;font-weight:700;margin-right:22px}
.topbar .auth{display:flex}
.topbar .auth a{padding:0 14px;border-left:1px solid rgba(255,255,255,.5);height:30px;display:flex;align-items:center}
.brand{position:absolute;left:162px;top:34px;display:flex;align-items:center;gap:12px}
.brand .dot{width:46px;height:46px;border-radius:50%;background:var(--green)}
.brand .name{font-weight:800;font-size:30px;color:var(--orange);letter-spacing:.5px}
.search{position:absolute;left:700px;top:52px;width:233px;height:33px;border:1px solid #cfcfcf;display:flex;align-items:center;padding-left:12px;gap:10px;font-size:9px;color:#777;letter-spacing:.3px}
.cart{position:absolute;left:957px;top:52px;display:flex;gap:8px;align-items:center}
.cart .label{font-size:9px;line-height:12px;color:#555;font-weight:600}
.cart .label b{display:block;color:var(--orange);font-size:12px}
.main-nav{position:absolute;left:546px;top:103px;display:flex;font-size:10.5px;font-weight:700}
.main-nav a{padding:6px 14px;color:#333}
.main-nav a.active{background:var(--green);color:#fff}

/* hero */
.hero{top:143px;height:435px;background:radial-gradient(ellipse at 50% 40%,#6d6a66 0%,#4b4946 55%,#2f2e2c 100%)}
.hero-title{position:absolute;left:462px;top:257px;width:276px;height:50px;background:rgba(247,143,32,.85);color:#fff;font-weight:700;font-size:22px;display:flex;align-items:center;justify-content:center}
.btn-shop{position:absolute;left:546px;top:315px;width:110px;height:36px;background:var(--green);color:#fff;font-weight:700;font-size:14px;display:flex;align-items:center;justify-content:center}
.dots{position:absolute;top:391px;left:0;width:100%;display:flex;justify-content:center;gap:14px}
.dots i{width:9px;height:9px;border-radius:50%;background:#fff;display:block}
.dots i.on{background:transparent;border:2px solid #fff}

/* tabs */
.tab{position:absolute;left:494px;top:-3px;width:218px;height:42px;background:var(--orange);color:#fff;font-weight:700;font-size:16px;display:flex;align-items:center;justify-content:center;clip-path:polygon(0 0,100% 0,91% 100%,9% 100%)}

/* products */
.products{top:578px;height:995px;background:var(--panel);border-top:3px solid var(--orange)}
.product-grid{position:absolute;left:162px;top:71px;display:grid;grid-template-columns:repeat(3,281px);column-gap:16px;row-gap:21px}
.product-card{background:#fff;height:278px;box-shadow:0 3px 6px rgba(0,0,0,.08)}
.product-card .photo{height:196px}
.product-card h3{font-size:12.5px;font-weight:700;color:var(--orange);margin:20px 0 0 18px}
.btn-view{display:inline-flex;align-items:center;gap:5px;margin:8px 0 0 18px;height:20px;padding:0 9px;background:var(--green);color:#fff;font-size:9.5px;font-weight:700}

/* eco + specials */
.eco{top:1573px;height:349px;background:#fff}
.eco-box{position:absolute;left:162px;top:34px;width:398px;height:273px;background:var(--orange);color:#fff;padding:30px 30px 0 104px}
.eco-box h2{font-size:19px;font-weight:700;line-height:25px}
.eco-box p{font-size:12px;line-height:21px;margin-top:12px}
.btn-read{display:inline-flex;align-items:center;justify-content:center;width:98px;height:28px;background:var(--green);color:#fff;font-size:9.5px;font-weight:700;margin-top:14px}
.specials{position:absolute;left:593px;top:34px;width:443px;height:273px;background:linear-gradient(180deg,#7f8a6c 0%,#6e7660 40%,#8d8d8b 60%,#5d5d5b 100%)}
.specials .copy{position:absolute;left:26px;top:204px;color:#fff}
.specials h2{font-size:23px;font-weight:800;line-height:24px}
.specials small{display:block;font-size:11.5px;font-weight:700;margin-top:3px}
.btn-special{position:absolute;left:285px;top:205px;width:136px;height:44px;background:var(--orange);color:#fff;font-weight:700;font-size:16px;display:flex;align-items:center;justify-content:center}

/* featured */
.featured{top:1922px;height:420px;background:linear-gradient(135deg,#cfcfcf,#bdbdbd 50%,#c9c9c9);border-top:3px solid var(--orange)}
.feature-row{position:absolute;left:162px;top:90px;display:flex;gap:19px}
.feature-card{width:207px;height:277px;background:#fff;padding:9px;box-shadow:0 3px 6px rgba(0,0,0,.1);position:relative}
.feature-card .photo{height:160px}
.feature-card h4{font-size:10px;font-weight:700;margin-top:14px;line-height:13px;color:#333}
.feature-card .price{font-size:15px;font-weight:700;color:var(--orange);margin-top:2px}
.feature-card .btn-add{position:absolute;left:9px;bottom:18px;height:22px;padding:0 10px;background:var(--green);color:#fff;font-size:9.5px;font-weight:700;display:flex;align-items:center;gap:5px}
.arrow{position:absolute;top:200px;width:44px;height:44px;border-radius:50%;background:#fff;display:flex;align-items:center;justify-content:center;box-shadow:0 2px 4px rgba(0,0,0,.15)}

/* call band */
.call-band{top:2342px;height:164px;background:var(--green);text-align:center;color:#2e2e2e}
.call-band h2{font-size:17px;font-weight:700;line-height:25px;margin-top:32px}
.call-numbers{display:flex;justify-content:center;align-items:center;gap:22px;margin-top:16px;font-family:"Roboto Condensed",Arial,sans-serif;font-size:28px}
.call-numbers .phone{width:38px;height:38px;border-radius:50%;background:#1e1e1e;display:flex;align-items:center;justify-content:center;margin-right:-8px}
.call-numbers .sep{width:2px;height:32px;background:#2e2e2e}

/* footer */
.site-footer{top:2506px;height:320px;background:var(--footer);color:#ddd}
.foot-brand{position:absolute;left:162px;top:48px;display:flex;align-items:center;gap:10px}
.foot-brand .dot{width:40px;height:40px;border-radius:50%;background:var(--green)}
.foot-brand .name{font-weight:800;font-size:25px;color:var(--orange)}
.follow{position:absolute;left:162px;top:164px;width:260px;text-align:center;font-size:10px;font-weight:700;color:#fff}
.social{display:flex;gap:8px;justify-content:center;margin-top:18px}
.social i{width:24px;height:24px;border-radius:50%;display:block}
.col{position:absolute;top:40px;font-size:10px;line-height:16.5px;color:#ccc}
.col h5{font-size:10px;font-weight:700;color:#fff;margin-bottom:14px}
.col-divider{position:absolute;top:40px;width:1px;height:220px;background:#555}
.foot-bottom{position:absolute;left:162px;top:254px;width:876px;border-top:1px solid #555;padding-top:22px;display:flex;justify-content:space-between;align-items:center;font-size:9px;color:#ccc}
.cards{display:flex;align-items:center;gap:6px}
.cards i{display:block;width:40px;height:24px;border-radius:3px;background:#e8e8e8}
</style>
</head>
<body>

<header class="block site-header">
  <div class="topbar">
    <svg width="12" height="12" viewBox="0 0 24 24"><path fill="#fff" d="M6.6 10.8c1.4 2.8 3.8 5.1 6.6 6.6l2.2-2.2c.3-.3.7-.4 1-.2 1.1.4 2.3.6 3.6.6.6 0 1 .4 1 1V20c0 .6-.4 1-1 1C10.6 21 3 13.4 3 4c0-.6.4-1 1-1h3.5c.6 0 1 .4 1 1 0 1.3.2 2.5.6 3.6.1.3 0 .7-.2 1z"/></svg>
    <span>CALL US NOW ON :</span><strong>0139-555-0182 / 0845-555-0145</strong>
    <div class="auth"><a href="#">Login</a><a href="#">Register</a></div>
  </div>
  <a class="brand" href="#"><span class="dot"></span><span class="name">PONDERMESH</span></a>
  <div class="search">
    <svg width="11" height="11" viewBox="0 0 24 24"><circle cx="10" cy="10" r="7" fill="none" stroke="#555" stroke-width="3"/><path d="M15 15l6 6" stroke="#555" stroke-width="3"/></svg>
    SEARCH PRODUCTS
  </div>
  <div class="cart">
    <svg width="30" height="24" viewBox="0 0 30 24"><path d="M1 2h5l4 13h14l4-9H8" fill="none" stroke="#555" stroke-width="2"/><circle cx="12" cy="20" r="2" fill="#555"/><circle cx="22" cy="20" r="2" fill="#555"/></svg>
    <div class="label">MY CART<b>$0.00</b></div>
  </div>
  <nav class="main-nav">
    <a class="active" href="#">HOME</a><a href="#">SHOP</a><a href="#">ABOUT US</a><a href="#">GROUND SOLUTIONS</a><a href="#">PONDERMESH</a><a href="#">CONTACT</a>
  </nav>
</header>

<section class="block hero" role="img" aria-label="Dark crushed stone filling a hexagonal grid">
  <div class="hero-title">PONDERMESH SYSTEM</div>
  <a class="btn-shop" href="#">SHOP NOW</a>
  <div class="dots"><i></i><i class="on"></i><i></i><i></i><i></i></div>
</section>

<section class="block products">
  <div class="tab">OUR PRODUCTS</div>
  <div class="product-grid">
    <article class="product-card"><div class="photo" role="img" aria-label="Geotextile membrane laid beside a wooden fence" style="background:linear-gradient(180deg,#c7c9c4 0%,#a38c6a 40%,#5d5d5a 100%)"></div><h3>GEOTEXTILE MEMBRANES</h3><a class="btn-view" href="#">&#9998; VIEW MORE</a></article>
    <article class="product-card"><div class="photo" role="img" aria-label="Wheelchair on a gravel driveway" style="background:linear-gradient(180deg,#3c4a5a 0%,#9a948a 45%,#c9c2b6 100%)"></div><h3>LIGHT DOMESTIC DRIVEWAYS</h3><a class="btn-view" href="#">&#9998; VIEW MORE</a></article>
    <article class="product-card"><div class="photo" role="img" aria-label="Gravel driveway with white grid path" style="background:linear-gradient(160deg,#b9a88d 0%,#d8cfbe 50%,#a99878 100%)"></div><h3>HEAVY DOMESTIC DRIVEWAYS</h3><a class="btn-view" href="#">&#9998; VIEW MORE</a></article>
    <article class="product-card"><div class="photo" role="img" aria-label="Excavator and workers laying grid on a commercial site" style="background:linear-gradient(180deg,#c6c8c8 0%,#8a8378 50%,#3e3d3a 100%)"></div><h3>COMMERCIAL PARKING SYSTEM</h3><a class="btn-view" href="#">&#9998; VIEW MORE</a></article>
    <article class="product-card"><div class="photo" role="img" aria-label="Shoe stepping on a stabilised gravel path" style="background:linear-gradient(180deg,#3d5574 0%,#8d8d8d 35%,#cfcbc3 100%)"></div><h3>PARKING AND PATHWAY SYSTEM</h3><a class="btn-view" href="#">&#9998; VIEW MORE</a></article>
    <article class="product-card"><div class="photo" role="img" aria-label="Black equestrian grid laid across a field" style="background:linear-gradient(180deg,#a9c3d8 0%,#5f7f4a 35%,#2a2a2a 70%,#4a4a4a 100%)"></div><h3>EQUESTRIAN GRID</h3><a class="btn-view" href="#">&#9998; VIEW MORE</a></article>
    <article class="product-card"><div class="photo" role="img" aria-label="Grass growing through reinforcement mesh" style="background:linear-gradient(160deg,#3f5a2a 0%,#6f9a3c 50%,#3a4f25 100%)"></div><h3>GRASS REINFORCEMENT MESH</h3><a class="btn-view" href="#">&#9998; VIEW MORE</a></article>
    <article class="product-card"><div class="photo" role="img" aria-label="Steel mesh pinned to grass" style="background:linear-gradient(160deg,#4c6a3a 0%,#7d9066 50%,#3f5431 100%)"></div><h3>STEEL U PINS</h3><a class="btn-view" href="#">&#9998; VIEW MORE</a></article>
    <article class="product-card"><div class="photo" role="img" aria-label="Metal garden edging beside flowering plants" style="background:linear-gradient(160deg,#2f4a25 0%,#8fa06e 45%,#c8c2b2 100%)"></div><h3>GARDEN EDGING</h3><a class="btn-view" href="#">&#9998; VIEW MORE</a></article>
  </div>
</section>

<section class="block eco">
  <div class="eco-box">
    <h2>PONDERMESH ECO<br>SOLUTIONS LTD</h2>
    <p>Stabilised Gravel Paving grids combines purpose designed Cellular reinforcement Pavers with the natural appearance, strength, security and free draining characteristics of a loose aggregate surface.</p>
    <a class="btn-read" href="#">READ MORE</a>
  </div>
  <div class="specials" role="img" aria-label="Silver car parked on a gravel driveway">
    <div class="copy"><h2>MONTHLY SPECIALS</h2><small>SPECIAL OFFER'S THIS MONTH</small></div>
    <a class="btn-special" href="#">SHOP NOW</a>
  </div>
</section>

<section class="block featured">
  <div class="tab">FEATURED PRODUCTS</div>
  <div class="arrow" style="left:125px"><svg width="12" height="14" viewBox="0 0 12 14"><path d="M9 1L3 7l6 6" fill="none" stroke="#333" stroke-width="2.5"/></svg></div>
  <div class="feature-row">
    <article class="feature-card"><div class="photo" role="img" aria-label="Bicycle wheel on gravel surface" style="background:linear-gradient(160deg,#4a4a48,#8e8b86 50%,#5a5856)"></div><h4>PONDERMESH 25 SYSTEM</h4><div class="price">£ 11.00</div><a class="btn-add" href="#">ADD TO CART</a></article>
    <article class="feature-card"><div class="photo" role="img" aria-label="Lorry wheels on a paving grid" style="background:linear-gradient(160deg,#8a8580,#5d5a56 50%,#a7a39c)"></div><h4>HEXAFORM 40 PAVING SYSTEM<br>FOR GRASS &amp; GRAVEL</h4><div class="price">£ 11.00</div><a class="btn-add" href="#">ADD TO CART</a></article>
    <article class="feature-card"><div class="photo" role="img" aria-label="Gravel inside white grid cells" style="background:linear-gradient(160deg,#b8ab98,#e2ddd4 55%,#c9c4bb)"></div><h4>PONDERMESH 25</h4><div class="price">£ 18.00</div><a class="btn-add" href="#">ADD TO CART</a></article>
    <article class="feature-card"><div class="photo" role="img" aria-label="Black paving grid panel" style="background:linear-gradient(160deg,#2b2b2b,#6a6a6a 50%,#3a3a3a)"></div><h4>PAVING CELL DATA SHEET</h4><div class="price">£ 21.00</div><a class="btn-add" href="#">ADD TO CART</a></article>
  </div>
  <div class="arrow" style="left:1031px"><svg width="12" height="14" viewBox="0 0 12 14"><path d="M3 1l6 6-6 6" fill="none" stroke="#333" stroke-width="2.5"/></svg></div>
</section>

<section class="block call-band">
  <h2>24 HOUR MESSAGING SERVICE<br>CALL US NOW ON</h2>
  <div class="call-numbers">
    <span class="phone"><svg width="18" height="18" viewBox="0 0 24 24"><path fill="#fff" d="M6.6 10.8c1.4 2.8 3.8 5.1 6.6 6.6l2.2-2.2c.3-.3.7-.4 1-.2 1.1.4 2.3.6 3.6.6.6 0 1 .4 1 1V20c0 .6-.4 1-1 1C10.6 21 3 13.4 3 4c0-.6.4-1 1-1h3.5c.6 0 1 .4 1 1 0 1.3.2 2.5.6 3.6.1.3 0 .7-.2 1z"/></svg></span>
    <span>0139-555-0182</span><span class="sep"></span><span>0845-555-0145</span>
  </div>
</section>

<footer class="block site-footer">
  <div class="foot-brand"><span class="dot"></span><span class="name">PONDERMESH</span></div>
  <div class="follow">FOLLOW US ON
    <div class="social"><i style="background:#3b5998"></i><i style="background:#1da1f2"></i><i style="background:#d32020"></i><i style="background:#4f7fb8"></i></div>
  </div>
  <div class="col-divider" style="left:442px"></div>
  <div class="col" style="left:497px">
    <h5>CONTACT US</h5>
    Harrowfield House,<br>Kelvin Trade Park Est,<br>Dunmore, G99 4XZ.
    <h5 style="margin-top:32px">CONTACT US BETWEEN</h5>
    9.30am - 4.30pm Mon - Fri
  </div>
  <div class="col-divider" style="left:670px"></div>
  <div class="col" style="left:725px">
    <h5>MENU</h5>
    Home<br>Shop<br>About us<br>Ground solutions<br>Pondermesh<br>Contact us
  </div>
  <div class="col-divider" style="left:850px"></div>
  <div class="col" style="left:904px">
    <h5>PRODUCTS</h5>
    Geotextile membranes<br>Light domestic driveways<br>Heavy domestic driveways<br>Parking and pathway system<br>Grass reinforcement mesh<br>Steel u pins<br>Commercial parking system<br>Hoofbase grid<br>Monthly specials<br>Garden edging
  </div>
  <div class="foot-bottom">
    <div class="cards">Cards Accepted&nbsp;&nbsp;<i></i><i></i><i></i><i></i></div>
    <span>Copyrights @ 2016 All Rights Reserved</span>
  </div>
</footer>

</body>
</html>
```